BRANDEMEIER & BRANDEMEIER,LLP NEEDS A NEW LETTERHEAD DESIGN

a conservative yet contemporary layout befitting a long established
firm, consistent with the times, some form of logo so it catches ones attention, and is
admirable, but portrays integrity
Updates

I would like to approve #22066987 Please advise how to do this as it’s confusing on the site so I can approve payment for the designer

Target Market(s)

real estate investors and building management people

Industry/Entity Type

Law Firm

Font styles to use
Serif

Colors

Designer to choose colors to be used in the design.

Requirements
Must have
• some form of conservative logo

```html
<!DOCTYPE html>
<html lang="en">
<head>
<meta charset="utf-8">
<title>Brandemeier &amp; Brandemeier, LLP — Letterhead</title>
<link href="https://fonts.googleapis.com/css2?family=Libre+Baskerville&family=Arimo:wght@400&display=swap" rel="stylesheet">
<style>
  :root {
    --backdrop: #dfe1e2;
    --paper: #ffffff;
    --ink-dark: #3c4650;
    --ink-body: #6f7378;
    --rule-light: #c9ccd0;
    --sign-tone: #d9dbde;
  }
  * { margin: 0; padding: 0; box-sizing: border-box; }
  html, body {
    width: 1200px; height: 784px; overflow: hidden;
    background: var(--backdrop);
  }
  .letterhead {
    position: absolute; left: 340px; top: 22px;
    width: 520px; height: 740px;
    background: var(--paper);
    box-shadow: 0 2px 10px rgba(0,0,0,0.12);
  }
  .corner-tab { position: absolute; }
  .corner-tab--top { top: 0; left: 150px; width: 44px; height: 5px; background: var(--ink-dark); }
  .corner-tab--top-light { top: 5px; left: 150px; width: 30px; height: 4px; background: var(--rule-light); }
  .corner-tab--side { right: 0; top: 40px; width: 5px; height: 40px; background: var(--ink-dark); }
  .corner-tab--side-light { right: 5px; top: 40px; width: 4px; height: 28px; background: var(--rule-light); }

  .firm-mark {
    position: absolute; left: 44px; top: 46px;
    display: flex; align-items: center; gap: 10px;
  }
  .firm-mark__square { width: 22px; height: 22px; background: var(--ink-dark); }
  .firm-mark__name {
    font-family: "Libre Baskerville", serif; font-size: 13px; line-height: 15px;
    color: var(--ink-dark); letter-spacing: 0.5px;
  }

  .letter-body {
    position: absolute; left: 44px; top: 108px; width: 430px;
    font-family: "Arimo", Arial, sans-serif; font-size: 8.6px; line-height: 12.4px;
    color: var(--ink-body);
  }
  .letter-body p { margin-bottom: 14px; }

  .signature {
    position: absolute; left: 44px; top: 470px; width: 120px; height: 40px;
    background: var(--sign-tone); border-radius: 3px;
  }

  .letter-footer { position: absolute; left: 0; right: 0; bottom: 26px; }
  .letter-footer__rule { display: flex; height: 4px; margin: 0 22px; }
  .letter-footer__rule span { display: block; height: 100%; }
  .rule-dark { background: var(--ink-dark); }
  .rule-light { background: var(--rule-light); }
  .letter-footer__contacts {
    display: flex; justify-content: space-between; align-items: center;
    margin: 6px 24px 0;
    font-family: "Arimo", Arial, sans-serif; font-size: 7px; color: var(--ink-dark);
  }
  .contact-item { display: flex; align-items: center; gap: 3px; white-space: nowrap; }
  .contact-item svg { width: 7px; height: 7px; }
</style>
</head>
<body>
  <main class="letterhead">
    <div class="corner-tab corner-tab--top"></div>
    <div class="corner-tab corner-tab--top-light"></div>
    <div class="corner-tab corner-tab--side"></div>
    <div class="corner-tab corner-tab--side-light"></div>

    <header class="firm-mark">
      <span class="firm-mark__square"></span>
      <div class="firm-mark__name">BRANDEMEIER &amp;<br>BRANDEMEIER, LLP</div>
    </header>

    <section class="letter-body">
      <p>Lorem Ipsum is simply dummy text of the printing and typesetting industry. Lorem Ipsum has been the industry's standard dummy text ever since the 1500s, when an unknown printer took a galley of type and scrambled it to make a type specimen book. It has survived not only five centuries, but also the leap into electronic typesetting, remaining essentially unchanged. It was popularised in the 1960s with the release of transfer sheets containing Lorem Ipsum passages, and more recently with desktop publishing software and layout programs including versions of Lorem Ipsum.</p>
      <p>It is a long established fact that a reader will be distracted by the readable content of a page when looking at its layout. The point of using Lorem Ipsum is that it has a more-or-less normal distribution of letters, as opposed to using 'Content here, content here', making it look like readable English. Many desktop publishing packages and web page editors now use Lorem Ipsum as their default model text, and a search for 'lorem ipsum' will uncover many web sites still in their infancy. Various versions have evolved over the years, sometimes by accident, sometimes on purpose (injected humour and the like).</p>
      <p>Contrary to popular belief, Lorem Ipsum is not simply random text. It has roots in a piece of classical Latin literature from 45 BC, making it over 2000 years old. A noted scholar and Latin professor at a small college looked up one of the more obscure Latin words, consectetur, from a Lorem Ipsum passage, and going through the cites of the word in classical literature, discovered the undoubtable source. Lorem Ipsum comes from sections 1.10.32 and 1.10.33 of an ancient treatise on ethics, with structures used to generate Lorem Ipsum which looks reasonable. The generated Lorem Ipsum is therefore always free from repetition, injected humour, or non-characteristic words etc.</p>
    </section>

    <div class="signature" role="img" aria-label="Handwritten signature of the sender"></div>

    <footer class="letter-footer">
      <div class="letter-footer__rule">
        <span class="rule-dark" style="width:20%"></span>
        <span class="rule-light" style="width:3%"></span>
        <span class="rule-dark" style="width:34%"></span>
        <span class="rule-light" style="width:3%"></span>
        <span class="rule-dark" style="width:22%"></span>
        <span class="rule-light" style="width:18%"></span>
      </div>
      <div class="letter-footer__contacts">
        <span class="contact-item">
          <svg viewBox="0 0 10 10"><path d="M5 0a3.5 3.5 0 0 0-3.5 3.5C1.5 6 5 10 5 10s3.5-4 3.5-6.5A3.5 3.5 0 0 0 5 0z" fill="#3c4650"/></svg>
          48 Harbor Lane Suite 210 Millbrook, New York 10990
        </span>
        <span class="contact-item">
          <svg viewBox="0 0 10 10"><rect width="10" height="10" rx="2" fill="#3c4650"/></svg>
          (555) 310-4827
        </span>
        <span class="contact-item">
          <svg viewBox="0 0 10 10"><rect width="10" height="10" rx="2" fill="#3c4650"/></svg>
          (555) 310-4829
        </span>
        <span class="contact-item">
          <svg viewBox="0 0 10 10"><rect width="10" height="10" rx="2" fill="#3c4650"/></svg>
          info@bbrelaw.com
        </span>
        <span class="contact-item">
          <svg viewBox="0 0 10 10"><circle cx="5" cy="5" r="5" fill="#3c4650"/></svg>
          www.brandemeierlaw.com
        </span>
      </div>
    </footer>
  </main>
</body>
</html>
```